2023 Cheers to 50 Years Graphic

Hi - I'd like a high-res image that's also print ready that we can use around our office with our 2023 slogan: Cheers to 50 years!

Ideally we'd like a catchy image, the slogan and our logo.

I'll attach the 2022 example. Please use our 50th anniversary logo also attached.

Graphic could be anything celebratory!

Main demographic is males.

Maybe cheers of champagne glasses or beer. But open top option that does not involve alcohol too.

```html
<!DOCTYPE html>
<html lang="en">
<head>
<meta charset="utf-8">
<title>2023 – Cheers to 50 years!</title>
<link rel="stylesheet" href="https://fonts.googleapis.com/css2?family=Lobster+Two:wght@700&display=swap">
<style>
  :root {
    --navy: #2e3a80;
    --spark-core: #fffefa;
    --spark-glow: #fdf0da;
    --spark-light: #f6d29c;
    --spark-gold: #e6a75c;
    --spark-amber: #c07a30;
    --spark-deep: #7a4a1a;
  }
  html, body {
    margin: 0;
    padding: 0;
    width: 1200px;
    height: 800px;
    overflow: hidden;
  }
  .poster {
    position: relative;
    width: 1200px;
    height: 800px;
    overflow: hidden;
    font-family: "Lobster Two", cursive;
    color: var(--navy);
  }
  .sparkler-backdrop {
    position: absolute;
    inset: 0;
    background:
      radial-gradient(ellipse 560px 430px at 640px 250px,
        var(--spark-core) 0%,
        var(--spark-core) 45%,
        rgba(253, 240, 218, 0.85) 70%,
        rgba(246, 210, 156, 0) 100%),
      radial-gradient(ellipse 380px 300px at 1080px 520px,
        rgba(255, 246, 230, 0.9) 0%,
        rgba(246, 210, 156, 0) 100%),
      radial-gradient(ellipse 300px 260px at 300px 560px,
        rgba(253, 232, 200, 0.7) 0%,
        rgba(246, 210, 156, 0) 100%),
      radial-gradient(ellipse 1000px 760px at 640px 300px,
        var(--spark-glow) 0%,
        var(--spark-light) 45%,
        var(--spark-gold) 70%,
        var(--spark-amber) 88%,
        var(--spark-deep) 100%);
  }
  .headline {
    position: absolute;
    margin: 0;
    font-weight: 700;
    line-height: 1;
    white-space: nowrap;
    transform: translateX(-50%);
  }
  .headline-year {
    top: 132px;
    left: 567px;
    font-size: 150px;
  }
  .headline-slogan {
    top: 300px;
    left: 592px;
    font-size: 134px;
  }
  .brand-mark {
    position: absolute;
    left: 862px;
    top: 586px;
    width: 268px;
    height: 150px;
    display: flex;
    align-items: center;
    justify-content: center;
    gap: 14px;
  }
  .brand-dot {
    width: 62px;
    height: 62px;
    border-radius: 50%;
    background: var(--navy);
    flex: none;
  }
  .brand-name {
    font-weight: 700;
    font-size: 44px;
    line-height: 1.05;
    white-space: nowrap;
  }
</style>
</head>
<body>
  <main class="poster">
    <div class="sparkler-backdrop" role="img" aria-label="Close-up photograph of a glowing golden sparkler bursting with sparks"></div>
    <h1 class="headline headline-year">2023</h1>
    <p class="headline headline-slogan">Cheers to 50 years!</p>
    <div class="brand-mark">
      <span class="brand-dot"></span>
      <span class="brand-name">Harborline<br>Supply</span>
    </div>
  </main>
</body>
</html>
```